Web Design For Manufacturing And Outsourcing Company

Pick up the pieces from our previous developer and help us complete our website.

5 pages - Home,Machining,Sourcing,About Us, and Contact

Attached you will find screen shots of previous direction but we're open to new ideas.

We can provide all text and images needed.

Thanks!

Number of Pages Required

5+ page

```html
<!DOCTYPE html>
<html lang="en">
<head>
<meta charset="utf-8">
<title>Kestrel Industries</title>
<link href="https://fonts.googleapis.com/css2?family=Lato:wght@400;700;900&display=swap" rel="stylesheet">
<style>
:root{
  --orange:#e5511f;
  --orange-deep:#c9441a;
  --ink:#2b2b2b;
  --text:#6b6b6b;
  --panel:#f4f4f4;
  --white:#ffffff;
  --footer:#3b3b3b;
  --line:#e2e2e2;
}
*{margin:0;padding:0;box-sizing:border-box}
html,body{width:1200px;height:2462px;overflow:hidden}
body{font-family:'Lato',sans-serif;color:var(--ink);background:var(--white);position:relative}
.abs{position:absolute}

.top-rule{left:0;top:0;width:1200px;height:3px;background:var(--orange)}
.site-header{left:0;top:3px;width:1200px;height:138px;background:var(--white)}
.brand{left:112px;top:46px;display:flex;align-items:center;gap:10px}
.brand-mark{width:22px;height:22px;background:var(--orange)}
.brand-name{font-weight:900;font-size:17px;letter-spacing:2px;color:var(--ink)}
.main-nav{left:476px;top:60px;display:flex;gap:0}
.main-nav a{font-weight:700;font-size:17px;color:var(--ink);text-decoration:none;position:absolute;white-space:nowrap}
.search-btn{left:1047px;top:52px;width:40px;height:40px;border-radius:50%;background:var(--orange)}

.hero{left:0;top:141px;width:1200px;height:620px;background:linear-gradient(120deg,#2a2622 0%,#5b4c3e 35%,#8a7a68 55%,#3d3833 80%,#1f1d1b 100%)}
.hero-title{left:112px;top:322px;color:var(--white);font-weight:900;text-transform:uppercase;line-height:1.2;text-shadow:0 2px 6px rgba(0,0,0,.35)}
.hero-title .sm{font-size:34px}
.hero-title .lg{font-size:52px}
.hero-arrow{top:410px;width:40px;height:40px;border-radius:50%;background:rgba(0,0,0,.7)}
.hero-cut{left:0;top:660px}

.service{top:758px;width:600px;height:573px}
.service.machining{left:0;background:var(--white)}
.service.sourcing{left:600px;background:var(--panel)}
.section-title{font-weight:900;font-size:37px;color:var(--ink);text-transform:uppercase}
.service .section-title{position:absolute;left:112px;top:82px}
.service.sourcing .section-title{left:68px}
.icon-ring{position:absolute;top:165px;width:110px;height:110px;border-radius:50%;background:var(--white);border:3px solid var(--line)}
.icon-ring span{position:absolute;left:28px;top:28px;width:48px;height:48px;border-radius:6px;background:linear-gradient(135deg,#f2a283,#e5511f 60%,#3b3b3b)}
.service-copy{position:absolute;left:112px;top:314px;width:425px;font-size:15px;line-height:26px;color:var(--text)}
.service.sourcing .service-copy{left:68px;width:420px}
.btn{position:absolute;display:flex;align-items:center;justify-content:center;gap:6px;font-weight:700;font-size:16px;text-transform:uppercase;border-radius:24px}
.btn-solid{background:var(--orange);color:var(--white)}
.btn-outline{border:2px solid #cfcfcf;color:var(--orange)}
.service .btn{left:112px;top:426px;width:175px;height:45px}
.service.sourcing .btn{left:68px}

.about-photo{left:0;top:1331px;width:600px;height:545px;background:linear-gradient(135deg,#c9ced2 0%,#8d959b 40%,#dde1e3 70%,#a66a46 100%)}
.about{left:600px;top:1331px;width:600px;height:545px;background:var(--white)}
.about .section-title{position:absolute;left:68px;top:92px}
.about-copy{position:absolute;left:68px;top:160px;width:420px;font-size:15px;line-height:25.8px;color:var(--text);text-align:justify}
.value{position:absolute;top:376px;width:110px;text-align:center}
.value-icon{display:block;margin:0 auto 12px;width:56px;height:56px;border-radius:50%;background:radial-gradient(circle,#f08a63 0%,#e5511f 45%,#3b3b3b 100%)}
.value-label{font-weight:900;font-size:17px;color:var(--ink)}

.cta{left:0;top:1876px;width:1200px;height:394px;background:radial-gradient(ellipse at 70% 60%,#ee6a35 0%,var(--orange) 45%,var(--orange-deep) 100%)}
.cta-title{position:absolute;left:0;top:98px;width:1200px;text-align:center;color:var(--white);font-weight:900;font-size:36px;line-height:54px;text-transform:uppercase}
.cta .btn{left:499px;top:238px;width:203px;height:51px;background:var(--white);color:var(--orange)}

.site-footer{left:0;top:2270px;width:1200px;height:192px;background:var(--footer);color:var(--white)}
.copyright{position:absolute;left:112px;top:68px;font-size:16px;line-height:31px}
.footer-brand{position:absolute;left:0;top:92px;width:1200px;text-align:center}
.footer-brand .brand-name{color:var(--white);font-size:16px}
.social{position:absolute;left:923px;top:79px;display:flex;gap:12px}
.social span{width:32px;height:32px;border-radius:50%;border:2px solid var(--white)}
</style>
</head>
<body>
<div class="abs top-rule"></div>

<header class="abs site-header">
  <div class="abs brand" style="top:43px">
    <span class="brand-mark"></span>
    <span class="brand-name">KESTREL INDUSTRIES</span>
  </div>
  <nav class="abs main-nav" style="left:0;top:60px;width:1200px;height:24px">
    <a style="left:476px">HOME</a>
    <a style="left:559px">MACHINING CAPABILITIES</a>
    <a style="left:801px">SOURCING</a>
    <a style="left:919px">CONTACT US</a>
  </nav>
  <div class="abs search-btn" style="top:49px">
    <svg width="40" height="40" viewBox="0 0 40 40"><circle cx="18" cy="18" r="6" fill="none" stroke="#fff" stroke-width="3"/><line x1="22.5" y1="22.5" x2="27" y2="27" stroke="#fff" stroke-width="3" stroke-linecap="round"/></svg>
  </div>
</header>

<section class="abs hero" role="img" aria-label="Close-up of a CNC milling machine spindle cutting a metal part with coolant hoses"></section>
<h1 class="abs hero-title">
  <span class="sm">A single point of</span><br>
  <span class="lg">Contact</span> <span class="sm">for all your</span><br>
  <span class="sm">procurement</span> <span class="lg">Needs</span>
</h1>
<div class="abs hero-arrow" style="left:42px">
  <svg width="40" height="40" viewBox="0 0 40 40"><polyline points="23,12 15,20 23,28" fill="none" stroke="#fff" stroke-width="3"/></svg>
</div>
<div class="abs hero-arrow" style="left:1116px">
  <svg width="40" height="40" viewBox="0 0 40 40"><polyline points="17,12 25,20 17,28" fill="none" stroke="#fff" stroke-width="3"/></svg>
</div>
<svg class="abs hero-cut" width="1200" height="102" viewBox="0 0 1200 102">
  <polygon points="0,92 600,8 1200,92 1200,102 0,102" fill="#e5511f"/>
  <polygon points="0,102 0,98 600,26 600,102" fill="#ffffff"/>
  <polygon points="600,26 1200,98 1200,102 600,102" fill="#f4f4f4"/>
</svg>

<section class="abs service machining">
  <h2 class="section-title">Machining</h2>
  <div class="icon-ring" style="left:111px" role="img" aria-label="Blueprint drafting icon"><span></span></div>
  <div class="icon-ring" style="left:249px" role="img" aria-label="Robotic arm on a conveyor icon"><span></span></div>
  <div class="icon-ring" style="left:385px" role="img" aria-label="Packaged box with handling marks icon"><span></span></div>
  <p class="service-copy">whether prototype, quick-turn, short or medium run roduction, our In-house capabilities can help you with any machining needs you may have.</p>
  <a class="btn btn-solid">Read more
    <svg width="15" height="15" viewBox="0 0 16 16"><circle cx="8" cy="8" r="8" fill="#fff"/><polyline points="6,4 10,8 6,12" fill="none" stroke="#e5511f" stroke-width="2.2"/></svg>
  </a>
</section>

<section class="abs service sourcing">
  <h2 class="section-title">Sourcing</h2>
  <div class="icon-ring" style="left:67px" role="img" aria-label="Route map board icon"><span></span></div>
  <div class="icon-ring" style="left:203px" role="img" aria-label="Checklist clipboard icon"><span></span></div>
  <div class="icon-ring" style="left:341px" role="img" aria-label="Delivery truck icon"><span></span></div>
  <p class="service-copy" style="text-align:justify">We offer a One Stop Shop solution by leveraging existing relationships and supply base knowledge to source hard to locate items, components and assemblies at the lowest cost</p>
  <a class="btn btn-outline">Read more
    <svg width="15" height="15" viewBox="0 0 16 16"><circle cx="8" cy="8" r="8" fill="#e5511f"/><polyline points="6,4 10,8 6,12" fill="none" stroke="#fff" stroke-width="2.2"/></svg>
  </a>
</section>

<div class="abs about-photo" role="img" aria-label="Engineer operating the touchscreen control panel of an industrial robot in a factory hall"></div>
<section class="abs about">
  <h2 class="section-title">About us</h2>
  <p class="about-copy">We are committed to consistently exceeding customer expectations by providing products, services and sourcing solutions of the highest standard of quality. With our streamlined processes our method is efficient, provides value and ensures on time delivery. Our success is based on continuously improving the efficiencies and effectiveness of our products, processes, and quality management systems.</p>
  <div class="value" style="left:65px"><span class="value-icon" role="img" aria-label="Teamwork icon"></span><span class="value-label">TEAMWORK</span></div>
  <div class="value" style="left:225px"><span class="value-icon" role="img" aria-label="Handshake respect icon"></span><span class="value-label">RESPECT</span></div>
  <div class="value" style="left:382px"><span class="value-icon" role="img" aria-label="Hands holding a gear icon"></span><span class="value-label">GRATITUDE</span></div>
</section>

<section class="abs cta" role="img" aria-label="Orange-tinted background of machined gears">
  <h2 class="cta-title">Contact us today with your machining<br>or sourcing needs!</h2>
  <a class="btn">Get in touch
    <svg width="15" height="15" viewBox="0 0 16 16"><circle cx="8" cy="8" r="8" fill="#e5511f"/><polyline points="6,4 10,8 6,12" fill="none" stroke="#fff" stroke-width="2.2"/></svg>
  </a>
</section>

<footer class="abs site-footer">
  <p class="copyright">© Copyright 2019 Kestrel Industries.<br>All Rights Reserved.</p>
  <div class="footer-brand"><span class="brand-name">KESTREL INDUSTRIES</span></div>
  <div class="social" aria-label="Social links">
    <span></span><span></span><span></span><span></span>
  </div>
</footer>
</body>
</html>
```